Business Card Design For A Cajun Seafood Restaurant

We are opening a cajun seafood restaurant in a week. We mainly serve cajun seafood which is orginally from Louisiana. We want design on both sides of a business card. I have menu on the website. You can go to www.reednkettle.example to check out our menu.

Restaurant name: Reed N' Kettle
Phone: +1 (555) 304-7712
Address: 48206 Ludlow Row, #7, Bexmoor Flats, Ca90000
Email: reednkettle@mailbox.example
Website: www.reednkettle.example

Maybe add social media icons (facebook, instagram) if looks nice on the business card.
facebook.com/reednkettle
instagram.com/reednkettle or @reednkettle

Attached is the logo and other business card samples that I like.

```html
<!DOCTYPE html>
<html lang="en">
<head>
<meta charset="utf-8">
<title>Reed N' Kettle — Business Card</title>
<link rel="stylesheet" href="https://fonts.googleapis.com/css2?family=Source+Sans+3:wght@400;600&display=swap">
<style>
  :root {
    --backdrop: #3a3a3a;
    --card: #fbfbfb;
    --orange: #f85c00;
    --yellow: #f7c300;
    --ink: #1c1c1c;
    --white: #ffffff;
  }
  * { margin: 0; padding: 0; box-sizing: border-box; }
  html, body { width: 1200px; height: 750px; overflow: hidden; }
  body {
    background: var(--backdrop);
    font-family: "Source Sans 3", sans-serif;
    position: relative;
  }
  .card {
    position: absolute;
    top: 228px;
    width: 462px;
    height: 262px;
    background: var(--card);
    border-radius: 14px;
    overflow: hidden;
  }
  .card--front { left: 124px; }
  .card--back { left: 618px; }

  .wave { position: absolute; inset: 0; width: 100%; height: 100%; }

  .brand {
    position: absolute;
    display: flex;
    align-items: center;
    gap: 8px;
    color: var(--ink);
    font-weight: 600;
    white-space: nowrap;
  }
  .brand__dot { border-radius: 50%; background: var(--orange); flex: none; }
  .card--front .brand { left: 48px; top: 62px; font-size: 20px; }
  .card--front .brand__dot { width: 26px; height: 26px; }
  .card--back .brand {
    left: 50%; top: 96px; transform: translateX(-50%);
    font-size: 26px;
  }
  .card--back .brand__dot { width: 40px; height: 40px; }

  .person {
    position: absolute;
    right: 20px;
    top: 44px;
    text-align: right;
  }
  .person__name { color: var(--orange); font-size: 18px; font-weight: 600; line-height: 1.2; }
  .person__title { color: var(--ink); font-size: 14px; line-height: 1.2; }

  .contacts {
    position: absolute;
    right: 20px;
    top: 173px;
    list-style: none;
    text-align: right;
    color: var(--white);
    font-size: 12.5px;
    line-height: 18px;
  }
  .contacts li { display: flex; justify-content: flex-end; align-items: center; gap: 5px; }
  .contacts svg { width: 11px; height: 11px; fill: var(--white); }
  .contacts .address { margin-top: 2px; }

  .socials {
    position: absolute;
    left: 0; right: 0;
    top: 220px;
    display: flex;
    justify-content: center;
    gap: 4px;
    font-size: 13px;
    color: var(--ink);
  }
  .socials span { display: flex; align-items: center; gap: 3px; }
  .socials i {
    width: 18px; height: 18px; border-radius: 50%;
    background: var(--orange); display: inline-block;
  }
</style>
</head>
<body>

<section class="card card--front">
  <svg class="wave" viewBox="0 0 462 262" aria-hidden="true">
    <path d="M0 152 C70 180 140 200 230 190 C180 205 90 200 0 170 Z" fill="var(--yellow)"/>
    <path d="M0 170 C110 212 230 220 320 180 C370 158 420 138 462 132 L462 262 L0 262 Z" fill="var(--orange)"/>
    <path d="M28 160 C120 200 230 200 310 165 C370 140 410 126 454 126 C410 130 370 146 312 172 C230 208 120 206 28 160 Z" fill="var(--ink)"/>
  </svg>

  <div class="brand"><span class="brand__dot"></span>Reed N' Kettle</div>

  <div class="person">
    <p class="person__name">DANA WHITLOW</p>
    <p class="person__title">CEO/Founder</p>
  </div>

  <ul class="contacts">
    <li>+1 (555) 304-7712
      <svg viewBox="0 0 24 24"><path d="M6.6 10.8a15.1 15.1 0 0 0 6.6 6.6l2.2-2.2a1 1 0 0 1 1-.25 11.4 11.4 0 0 0 3.6.57 1 1 0 0 1 1 1V20a1 1 0 0 1-1 1A17 17 0 0 1 3 4a1 1 0 0 1 1-1h3.5a1 1 0 0 1 1 1c0 1.25.2 2.45.57 3.57a1 1 0 0 1-.25 1z"/></svg>
    </li>
    <li>reednkettle@mailbox.example
      <svg viewBox="0 0 24 24"><path d="M2 5h20v14H2z M2 5l10 8 10-8" fill="var(--white)" stroke="var(--orange)" stroke-width="1.5"/></svg>
    </li>
    <li>www.reednkettle.example
      <svg viewBox="0 0 24 24"><circle cx="12" cy="12" r="10"/><path d="M2 12h20M12 2c3 3 3 17 0 20M12 2c-3 3-3 17 0 20" fill="none" stroke="var(--orange)" stroke-width="1.5"/></svg>
    </li>
    <li class="address">48206 Ludlow Row, #7, Bexmoor Flats, Ca90000</li>
  </ul>
</section>

<section class="card card--back">
  <div class="brand"><span class="brand__dot"></span>Reed N' Kettle</div>
  <div class="socials">
    <span><i></i>reednkettle</span>
    <span><i></i>@reednkettle</span>
  </div>
</section>

</body>
</html>
```